Meal Plan Website Needs New Pages Designed

Brightwick Supper Kits is an online, membership based program that delivers weekly meal programs (7 days worth of recipes plus shopping lists) carefully crafted by an expert team of meal planners. All recipes are created to comply with the following macronutrient ratio: 65% healthy fats, 25% lean protein, 10% good carbs.
All recipes are Paleo friendly and a great resource for those individuals who want to correctly implement this type of diet.

We are re-designing our website and need the following pages designed:

· Home page w/ logo
· How it works page
· Get Started! page
· Recipes Page template (these will be the pages on our site that will have recipes)
· Kitchen Essentials Training page (this will be a page with videos and tips + tricks, PDFs, etc)

So 5 total PSDs, 1 for each page.

Target audience: Men and women between the ages of 30 and 60 who want to:
· Eat healthy
· Lose weight
· Follow/Implement the Paleo diet
· Take the guesswork out of preparing delicious AND healthy meals for them and their families
· Know exactly what to eat, what to buy, how to make it

Feelings/Messages we want to communicate through the design:
· “Organic” but elegant look
· Fresh/light/Airy
· Simple but NOT GENERIC
· “I want to get cooking” feeling

Our Stylistic preferences:
· Minimalist with a few bold elements (something in between)
· Easy to visually navigate (enough white space, but not too much)
· There is more to “see” than to “read”

Our Color Preferences:
· Lighter pallet
· Colors that evoke natural woods, granite countertops…
· Stay away from using all dark colors

Our Font Type Preferences:
· Easy to read
· Not more than 3 font types
· Not too rigid
· Not too sophisticated
· Simple with a touch

Examples of Website Designs that we like:
· http://www.dorvanta.com/meal-plans/
· http://grulvix.com/
· https://www.mistobarn.com/

```html
<!DOCTYPE html>
<html lang="en">
<head>
<meta charset="utf-8">
<title>Brightwick Supper Kits</title>
<link href="https://fonts.googleapis.com/css2?family=Open+Sans:wght@400;600;700&display=swap" rel="stylesheet">
<style>
:root{
  --cream:#f1ecdc;
  --cream-dark:#e6dfca;
  --paper:#fbf9f3;
  --teal:#3e5957;
  --teal-deep:#324a48;
  --teal-light:#587472;
  --coral:#e9655b;
  --ink:#3b3b3b;
  --muted:#7d7a70;
  --line:#d9d2bd;
  --white:#ffffff;
}
*{box-sizing:border-box;margin:0;padding:0}
html,body{width:1200px;height:2284px;overflow:hidden}
body{font-family:"Open Sans",Arial,sans-serif;color:var(--ink);background:var(--cream)}
.wrap{width:840px;margin:0 auto;position:relative}

/* header */
.site-header{height:112px;background:var(--white)}
.site-header .wrap{height:112px;display:flex;align-items:center;justify-content:space-between}
.brand{display:flex;align-items:center;gap:12px}
.brand-dot{width:30px;height:30px;border-radius:50%;background:var(--teal)}
.brand-name{font-size:26px;font-weight:600;color:var(--teal)}
.account{display:flex;gap:8px}
.btn-small{font-size:10px;font-weight:700;letter-spacing:.5px;padding:7px 14px;border-radius:2px}
.btn-login{background:var(--cream-dark);color:var(--teal)}
.btn-join{background:var(--teal);color:var(--white)}

/* nav */
.main-nav{height:36px;background:var(--cream-dark);border-top:1px solid var(--line);border-bottom:1px solid var(--line)}
.main-nav .wrap{height:36px;display:flex;align-items:center}
.main-nav a{font-size:10px;font-weight:600;color:var(--teal);text-decoration:none;margin-right:34px;letter-spacing:.4px}
.main-nav a.active{color:var(--coral)}
.search{margin-left:auto}

/* hero */
.hero{height:412px;position:relative;background:radial-gradient(circle at 52% 28%,#d9762f 0,#a8552a 14%,#5a3a2a 34%,#3b2e26 60%),#3b2e26;overflow:hidden}
.hero-food{position:absolute;left:0;right:0;bottom:0;height:300px;background:linear-gradient(90deg,#5e8a2c 0%,#7a9a3a 25%,#b8472e 55%,#cf3a2a 68%,#6f9440 85%,#8a6a40 100%);opacity:.9}
.hero-caption{position:absolute;left:140px;top:112px;font-size:13px;color:var(--white);background:rgba(0,0,0,.35);padding:6px 10px}
.hero-arrow{position:absolute;top:190px;width:28px;height:28px;border-radius:50%;background:rgba(255,255,255,.85);display:flex;align-items:center;justify-content:center}
.hero-arrow.prev{left:14px}
.hero-arrow.next{right:14px}

/* stats */
.stats{height:220px;background:var(--teal)}
.stats .wrap{display:flex;justify-content:space-between;padding-top:68px}
.stat{width:260px;text-align:center;color:var(--white)}
.stat-value{font-size:44px;font-weight:700;line-height:1}
.stat-label{font-size:30px;font-weight:700;line-height:1.2;margin-top:2px}
.stat-note{font-size:13px;margin-top:2px}

/* features */
.features{height:250px}
.features .wrap{display:flex;justify-content:space-between;padding-top:62px}
.feature{width:250px;text-align:center}
.feature-icon{width:52px;height:52px;border-radius:50%;background:var(--teal);margin:0 auto 14px;display:flex;align-items:center;justify-content:center}
.feature h3{font-size:13px;font-weight:600;color:var(--teal);letter-spacing:.5px;margin-bottom:8px}
.feature p{font-size:10px;line-height:1.45;color:var(--muted);padding:0 24px}

/* programs */
.programs{height:1030px}
.programs-head{display:flex;justify-content:space-between;align-items:flex-end;padding-top:42px;padding-bottom:8px;border-bottom:1px solid var(--line)}
.programs-head h2{font-size:14px;font-weight:700;color:var(--ink);letter-spacing:.4px}
.view-all{font-size:10px;color:var(--coral);font-weight:600}
.program-grid{display:grid;grid-template-columns:repeat(3,250px);column-gap:45px;row-gap:40px;margin-top:40px}
.program-card{height:380px;background:var(--paper);border:1px solid var(--line);padding:14px 14px 0}
.program-card h4{font-size:13px;font-weight:600;color:var(--ink)}
.program-meta{font-size:8px;color:var(--muted);margin:6px 0 10px;text-transform:uppercase}
.program-photo{height:170px}
.program-card p{font-size:10px;line-height:1.5;color:var(--muted);margin-top:12px}
.read-more{display:block;width:72px;margin:18px 0 0 auto;background:var(--coral);color:var(--white);font-size:9px;font-weight:700;text-align:center;padding:7px 0;border-radius:2px}
.photo-a{background:linear-gradient(135deg,#7a5a3e,#c9a27a 55,#4f3a2a)}
.photo-b{background:linear-gradient(135deg,#3a2a22,#a25a3a 50%,#d78f52)}
.photo-c{background:linear-gradient(135deg,#e7e2da,#6a5e58 60%,#2f2a28)}
.photo-d{background:linear-gradient(135deg,#cfc7b2,#8a7a5e 50%,#4e4a3e)}
.photo-e{background:linear-gradient(135deg,#3e5a2a,#c9a03a 50%,#7a5a2a)}
.photo-f{background:linear-gradient(135deg,#2a2a22,#a24a2a 45%,#d9b24a)}

/* footer */
.site-footer{height:180px;background:var(--teal);color:var(--white)}
.site-footer .wrap{display:flex;justify-content:space-between;padding-top:14px}
.site-footer h5{font-size:11px;font-weight:700;letter-spacing:.5px;margin-bottom:8px}
.footer-col{width:240px}
.service-list{list-style:none;font-size:10px;line-height:15px}
.service-list li{display:flex;align-items:center;gap:6px}
.service-list li::before{content:"";width:4px;height:4px;background:var(--coral);border-radius:50%}
.social{display:flex;gap:8px;margin-bottom:16px}
.social span{width:20px;height:20px;border-radius:50%;background:var(--coral)}
.newsletter-title{font-size:10px;font-weight:700;margin-bottom:4px}
.newsletter-text{font-size:9px;line-height:1.4;color:#d7e0de;margin-bottom:10px}
.newsletter-form{display:flex}
.newsletter-form .field{width:150px;height:24px;background:var(--white);font-size:9px;color:var(--muted);padding:6px 8px}
.newsletter-form .submit{height:24px;background:var(--coral);font-size:9px;font-weight:700;padding:6px 10px}
.about-text{font-size:10px;line-height:1.5;color:#d7e0de}
.about-btn{display:inline-block;margin:12px 0 0 60px;background:var(--coral);font-size:9px;font-weight:700;padding:7px 16px;border-radius:2px}

.bottom-bar{height:44px;background:var(--teal-deep);color:#c6d1cf;font-size:9px}
.bottom-bar .wrap{height:44px;display:flex;align-items:center;justify-content:space-between}
.legal span{margin-right:14px}
</style>
</head>
<body>

<header class="site-header">
  <div class="wrap">
    <div class="brand"><span class="brand-dot"></span><span class="brand-name">Brightwick Supper Kits</span></div>
    <div class="account"><span class="btn-small btn-login">LOGIN</span><span class="btn-small btn-join">JOIN NOW</span></div>
  </div>
</header>

<nav class="main-nav">
  <div class="wrap">
    <a class="active">HOME</a><a>MEAL PLANS</a><a>ABOUT</a><a>HOW IT WORKS</a><a>RESOURCES</a><a>BLOG</a>
    <svg class="search" width="12" height="12" viewBox="0 0 12 12"><circle cx="5" cy="5" r="3.6" fill="none" stroke="#3e5957" stroke-width="1.5"/><line x1="7.6" y1="7.6" x2="11" y2="11" stroke="#3e5957" stroke-width="1.5"/></svg>
  </div>
</nav>

<section class="hero">
  <div class="hero-food" role="img" aria-label="Fresh vegetables on a wooden table: lettuce, tomatoes, peppers, cucumbers, mushrooms and potatoes"></div>
  <div class="hero-caption">Answers to All Your Questions About Brightwick Supper Kits</div>
  <span class="hero-arrow prev"><svg width="10" height="10" viewBox="0 0 10 10"><path d="M6.5 1.5 3 5l3.5 3.5" fill="none" stroke="#3e5957" stroke-width="1.6"/></svg></span>
  <span class="hero-arrow next"><svg width="10" height="10" viewBox="0 0 10 10"><path d="M3.5 1.5 7 5 3.5 8.5" fill="none" stroke="#3e5957" stroke-width="1.6"/></svg></span>
</section>

<section class="stats">
  <div class="wrap">
    <div class="stat"><div class="stat-value">65%</div><div class="stat-label">HEALTHY FATS</div><div class="stat-note">Per Week</div></div>
    <div class="stat"><div class="stat-value">25%</div><div class="stat-label">LEAN PROTEIN</div><div class="stat-note">Per Week</div></div>
    <div class="stat"><div class="stat-value">10%</div><div class="stat-label">GOOD CARBS</div><div class="stat-note">Per Week</div></div>
  </div>
</section>

<section class="features">
  <div class="wrap">
    <div class="feature">
      <div class="feature-icon"><svg width="24" height="24" viewBox="0 0 24 24"><path d="M3 12h18a9 9 0 0 1-18 0z" fill="#fff"/><rect x="10" y="5" width="4" height="5" rx="1" fill="#fff"/></svg></div>
      <h3>MEAL PLANS</h3>
      <p>Cras metus elit, commodo vel pretium sed, sollicitudin eget tellus. Cras lacinia laoreet libero et mattis.</p>
    </div>
    <div class="feature">
      <div class="feature-icon"><svg width="24" height="24" viewBox="0 0 24 24"><rect x="5" y="4" width="14" height="16" rx="1" fill="none" stroke="#fff" stroke-width="2"/><line x1="8" y1="9" x2="16" y2="9" stroke="#fff" stroke-width="1.6"/><line x1="8" y1="13" x2="16" y2="13" stroke="#fff" stroke-width="1.6"/></svg></div>
      <h3>QUICK START GUIDE</h3>
      <p>Cras metus elit, commodo vel pretium sed, sollicitudin eget tellus. Cras lacinia laoreet libero et mattis.</p>
    </div>
    <div class="feature">
      <div class="feature-icon"><svg width="24" height="24" viewBox="0 0 24 24"><path d="M12 3 21 20H3z" fill="#fff"/></svg></div>
      <h3>OUR MEMBERSHIP</h3>
      <p>Cras metus elit, commodo vel pretium sed, sollicitudin eget tellus. Cras lacinia laoreet libero et mattis.</p>
    </div>
  </div>
</section>

<section class="programs">
  <div class="wrap">
    <div class="programs-head"><h2>OUR PROGRAMS</h2><span class="view-all">View ALL</span></div>
    <div class="program-grid">
      <article class="program-card">
        <h4>Nullam elit diam, rhoncus sed</h4>
        <div class="program-meta">January 14, 2014 | 0 Comments</div>
        <div class="program-photo photo-a" role="img" aria-label="Cook seasoning a dish at a kitchen counter"></div>
        <p>Donec vel turpis non erat lacinia rhoncus. Quisque commodo venenatis arcu, non volutpat eros.</p>
        <span class="read-more">READ MORE</span>
      </article>
      <article class="program-card">
        <h4>Donec vel turpis non erat</h4>
        <div class="program-meta">January 14, 2014 | 0 Comments</div>
        <div class="program-photo photo-b" role="img" aria-label="Grilled meat on a barbecue"></div>
        <p>Donec vel turpis non erat lacinia rhoncus. Quisque commodo venenatis arcu, non volutpat eros.</p>
        <span class="read-more">READ MORE</span>
      </article>
      <article class="program-card">
        <h4>Quisque commodo venenatis</h4>
        <div class="program-meta">January 14, 2014 | 0 Comments</div>
        <div class="program-photo photo-c" role="img" aria-label="Chef plating food in a kitchen"></div>
        <p>Donec vel turpis non erat lacinia rhoncus. Quisque commodo venenatis arcu, non volutpat eros.</p>
        <span class="read-more">READ MORE</span>
      </article>
      <article class="program-card">
        <h4>Donec imperdiet nibh</h4>
        <div class="program-meta">January 14, 2014 | 0 Comments</div>
        <div class="program-photo photo-d" role="img" aria-label="Hands preparing food on a cutting board"></div>
        <p>Donec vel turpis non erat lacinia rhoncus. Quisque commodo venenatis arcu, non volutpat eros.</p>
        <span class="read-more">READ MORE</span>
      </article>
      <article class="program-card">
        <h4>Cras metus elit</h4>
        <div class="program-meta">January 14, 2014 | 0 Comments</div>
        <div class="program-photo photo-e" role="img" aria-label="Plated meal with vegetables"></div>
        <p>Donec vel turpis non erat lacinia rhoncus. Quisque commodo venenatis arcu, non volutpat eros.</p>
        <span class="read-more">READ MORE</span>
      </article>
      <article class="program-card">
        <h4>Nullam elit diam, rhoncus sed</h4>
        <div class="program-meta">January 14, 2014 | 0 Comments</div>
        <div class="program-photo photo-f" role="img" aria-label="Vegetables sizzling in a frying pan"></div>
        <p>Donec vel turpis non erat lacinia rhoncus. Quisque commodo venenatis arcu, non volutpat eros.</p>
        <span class="read-more">READ MORE</span>
      </article>
    </div>
  </div>
</section>

<footer class="site-footer">
  <div class="wrap">
    <div class="footer-col">
      <h5>CUSTOMER SERVICES</h5>
      <ul class="service-list">
        <li>Login</li><li>Signup</li><li>Recipes</li><li>Resources</li><li>Meal Plans</li><li>Testimonials</li><li>Programs</li><li>Contact Us</li>
      </ul>
    </div>
    <div class="footer-col">
      <h5>CONNECT US</h5>
      <div class="social"><span></span><span></span><span></span><span></span><span></span></div>
      <div class="newsletter-title">GET OUR NEWSLETTER</div>
      <div class="newsletter-text">Sign up to get our weekly plans, recipes and cooking tips.</div>
      <div class="newsletter-form"><span class="field">Enter Your Email</span><span class="submit">SUBMIT</span></div>
    </div>
    <div class="footer-col">
      <h5>ABOUT US</h5>
      <p class="about-text">Donec vel turpis non erat lacinia rhoncus sed nec mauris. Quisque commodo venenatis arcu, non volutpat eros. Nullam elit diam, rhoncus sed dapibus at, tempus vel velit. Cras metus elit, pretium.</p>
      <span class="about-btn">READ MORE</span>
    </div>
  </div>
</footer>

<div class="bottom-bar">
  <div class="wrap">
    <div class="legal"><span>Terms of Service</span><span>Privacy Policy</span><span>Sitemap</span></div>
    <div>Copyright 2014 Brightwick Supper Kits. All rights reserved.</div>
  </div>
</div>

</body>
</html>
```